Redesign of business card for Cedar Ridge Mechanical

We are looking for a new design for our business cards for Cedar Ridge Mechanical. We are a plumbing & HVAC construction company, operating on the West Coast of Canada and USA. Logo attached.
Industry/Entity Type
Construction - Plumbing & HVAC
Contact Information for Business Card
Name, address, phone numbers, email, website address
Look and feel
Each slider illustrates characteristics of the customer's brand and the style your logo design should communicate.

```html
<!DOCTYPE html>
<html lang="en">
<head>
<meta charset="utf-8">
<title>Cedar Ridge Mechanical – Business Card</title>
<link href="https://fonts.googleapis.com/css2?family=Montserrat:wght@400;700&display=swap" rel="stylesheet">
<style>
  :root {
    --stage: #2b2b2b;
    --card: #ffffff;
    --ink: #111111;
    --ink-soft: #333333;
  }
  * { margin: 0; padding: 0; box-sizing: border-box; }
  html, body {
    width: 1200px; height: 689px; overflow: hidden;
    background: var(--stage);
    font-family: "Montserrat", sans-serif;
    color: var(--ink);
  }
  .stage {
    width: 1200px; height: 689px;
    display: flex; align-items: center; justify-content: center; gap: 40px;
  }
  .card {
    width: 540px; height: 310px;
    background: var(--card);
    border-radius: 22px;
    position: relative;
    box-shadow: 0 10px 30px rgba(0,0,0,.45);
  }
  /* front */
  .card--front { display: flex; align-items: center; justify-content: center; }
  .brand { display: flex; align-items: center; gap: 14px; }
  .brand__square { width: 34px; height: 34px; background: var(--ink); flex: none; }
  .brand__name {
    font-weight: 700; font-size: 27px; letter-spacing: 1px;
    text-transform: uppercase; line-height: 1.1;
  }
  /* back */
  .card--back .brand { position: absolute; left: 34px; top: 130px; gap: 10px; }
  .card--back .brand__square { width: 22px; height: 22px; }
  .card--back .brand__name { font-size: 15px; letter-spacing: .5px; }
  .divider {
    position: absolute; left: 268px; top: 70px;
    width: 1.5px; height: 150px; background: var(--ink);
  }
  .contact { position: absolute; left: 290px; top: 66px; }
  .contact__name { font-weight: 700; font-size: 22px; letter-spacing: .5px; text-transform: uppercase; }
  .contact__role { font-size: 13px; color: var(--ink-soft); margin-top: 2px; }
  .contact__list { list-style: none; margin-top: 16px; }
  .contact__list li {
    display: flex; align-items: center; gap: 8px;
    font-size: 12.5px; line-height: 24px; color: var(--ink-soft);
  }
  .icon { width: 12px; height: 12px; fill: var(--ink); flex: none; }
  .address {
    position: absolute; right: 36px; bottom: 28px;
    font-size: 13px; color: var(--ink-soft);
  }
</style>
</head>
<body>
<main class="stage">
  <section class="card card--front" aria-label="Card front">
    <div class="brand">
      <span class="brand__square"></span>
      <span class="brand__name">Cedar Ridge<br>Mechanical</span>
    </div>
  </section>

  <section class="card card--back" aria-label="Card back">
    <div class="brand">
      <span class="brand__square"></span>
      <span class="brand__name">Cedar Ridge<br>Mechanical</span>
    </div>
    <span class="divider"></span>
    <div class="contact">
      <p class="contact__name">Daniel Hart</p>
      <p class="contact__role">Managing Director</p>
      <ul class="contact__list">
        <li>
          <svg class="icon" viewBox="0 0 24 24" aria-hidden="true"><path d="M6.6 10.8a15 15 0 0 0 6.6 6.6l2.2-2.2a1 1 0 0 1 1-.25 11.4 11.4 0 0 0 3.6.57 1 1 0 0 1 1 1V20a1 1 0 0 1-1 1A17 17 0 0 1 3 4a1 1 0 0 1 1-1h3.5a1 1 0 0 1 1 1c0 1.25.2 2.45.57 3.57a1 1 0 0 1-.25 1z"/></svg>
          123 456 789
        </li>
        <li>
          <svg class="icon" viewBox="0 0 24 24" aria-hidden="true"><path d="M2 5h20v14H2z" fill="none" stroke="#111" stroke-width="2"/><path d="M2 5l10 8 10-8" fill="none" stroke="#111" stroke-width="2"/></svg>
          info@cedarridgemech.com
        </li>
        <li>
          <svg class="icon" viewBox="0 0 24 24" aria-hidden="true"><circle cx="12" cy="12" r="10" fill="none" stroke="#111" stroke-width="2"/><path d="M2 12h20M12 2c3 3 3 17 0 20M12 2c-3 3-3 17 0 20" fill="none" stroke="#111" stroke-width="1.6"/></svg>
          www.cedarridgemech.com
        </li>
      </ul>
    </div>
    <p class="address">Your address, City State, Zip 1234</p>
  </section>
</main>
</body>
</html>
```